1 Banner für Affiliate-Marketing (Börse/Trading)
Zielgruppe
Wir vermitteln Kunden an einen Broker. Die Kunden eröffnen Handelskonten, in denen sie selbständig Finanzprodukte (CFDs, Forex, Aktien, Edelmetalle,...) gehebelt handeln. Wir bieten dem Kunden eine Dienstleistung an, indem wir Broker vorauswählen, technischen Support liefern, bei der Kontoeröffnung unterstützen und auf Wunsch auch Trader ausbilden.
Zielgruppe: männlich, finanz- und risikoaffin, Spekulant
Aufgabenstellung
Wir benötigen 1 klickstarken Banner für das Affiliate-Marketing
Bannergröße: 300*250
Formate: GIF, PNG, JPG, Vektor
Gerne auch animierte Vorschläge, aber bitte nicht ausschließlich.
Zusätzliche Info, die verarbeitet werden kann (aber nicht muss): Kelvora Bank hat in 2016 bei 2 Kundenumfragen den Testsieg als bester Broker gewonnen.
Design ist frei und muss sich nicht an der Homepage orientieren - vielmehr suchen wir klickstarke Banner aus der Finanz-/Börsenwelt mit Bildern Ihrer Wahl.

```html
<!DOCTYPE html>
<html lang="de">
<head>
<meta charset="utf-8">
<title>Kelvora Bank – Banner 300x250</title>
<link href="https://fonts.googleapis.com/css2?family=Lato:ital,wght@0,400;0,700;1,400;1,700&display=swap" rel="stylesheet">
<style>
  :root {
    --stage-edge: #e9e9e9;
    --stage-mid: #f6f6f6;
    --page: #ffffff;
    --label: #b3b3b3;
    --navy: #26305c;
    --orange: #f26a10;
    --highlight: #f6a821;
    --white: #ffffff;
    --photo-dark: #0f2150;
    --photo-mid: #2c4f9c;
    --photo-light: #e7ecf5;
    --badge: rgba(232, 238, 248, 0.92);
  }
  * { margin: 0; padding: 0; box-sizing: border-box; }
  html, body { width: 1200px; height: 1010px; overflow: hidden; }
  body {
    background: var(--page);
    font-family: "Lato", Arial, sans-serif;
    position: relative;
  }
  .stage {
    position: absolute; left: 0; top: 0; width: 1200px; height: 906px;
    background: radial-gradient(ellipse at 50% 50%, var(--stage-mid) 0%, var(--stage-mid) 40%, var(--stage-edge) 100%);
  }
  .size-label {
    position: absolute; top: 158px; left: 0; width: 1178px; text-align: center;
    font-size: 29px; font-weight: 700; font-style: italic; color: var(--label);
  }
  .banner {
    position: absolute; left: 318px; top: 269px; width: 569px; height: 474px;
    overflow: hidden; background: var(--white);
    box-shadow: 0 12px 40px rgba(0,0,0,0.22);
  }
  .banner-header {
    height: 74px; display: flex; align-items: center; justify-content: center; gap: 14px;
  }
  .brand-square {
    width: 22px; height: 22px; background: var(--navy);
  }
  .brand-name {
    color: var(--navy); font-size: 50px; font-weight: 700; font-style: normal;
  }
  .hero {
    position: absolute; left: 0; top: 74px; width: 569px; height: 400px;
    background: linear-gradient(180deg, var(--photo-dark) 0%, var(--photo-mid) 55%, var(--photo-light) 100%);
  }
  .headline {
    position: absolute; left: 0; top: 92px; width: 569px; text-align: center;
    color: var(--white); font-style: italic; font-size: 27px; line-height: 38px;
  }
  .headline .mark { background: var(--highlight); padding: 0 4px; }
  .price-badge {
    position: absolute; left: 27px; top: 265px; width: 168px; height: 168px;
    border-radius: 50%; background: var(--badge);
    display: flex; flex-direction: column; align-items: center; justify-content: center;
    color: var(--navy); font-style: italic; font-size: 25px; line-height: 33px;
  }
  .price-badge strong { font-weight: 700; }
  .cta {
    position: absolute; left: 277px; top: 376px; width: 271px; height: 68px;
    background: var(--orange); color: var(--white);
    display: flex; align-items: center; justify-content: center; gap: 12px;
    font-size: 28px; font-style: italic; font-weight: 400;
  }
</style>
</head>
<body>
  <div class="stage"></div>
  <div class="size-label">300X250</div>

  <div class="banner">
    <div class="banner-header">
      <span class="brand-square" aria-hidden="true"></span>
      <span class="brand-name">Kelvora Bank</span>
    </div>
    <div class="hero" role="img" aria-label="Börsenchart mit steigender Kurslinie, davor Figuren von Bulle und Bär"></div>
    <p class="headline">Mehrfacher Testsieg<span class="mark">als BESTER BROKER</span><br>in 2016</p>
    <div class="price-badge">
      <strong>GER30</strong>
      <span>günstiger</span>
      <span>ist keiner</span>
    </div>
    <a class="cta">KLICKEN HIER
      <svg width="12" height="18" viewBox="0 0 12 18" aria-hidden="true"><path d="M1 1 L11 9 L1 17 Z" fill="#ffffff"/></svg>
    </a>
  </div>
</body>
</html>
```